sydney wedding photography business needs a business card design

we need a business card design for a sydney based wedding photography and videography business. our business name is :golden hour studio and film. our target clients are 24-35 yrs female. our style is candid, organic, natural, dynamic. we are a team of young photographers and videographers, and help brides to create memories that they will cherish for the rest of their lives. the logo will be provided. we want an elegant design that reflects our style, and also want to give a great impression to our clients that we are one of the best studios in sydney and our brand means quality and premium service.

Target Market(s)

bride to be, 24-35 years old, living in sydney and surrunding areas

Industry/Entity Type

Wedding Photography

Contact Information for Business Card

address: 57 tarrant street, glenmore nsw 2047
mobile: 0431872259
phone: (02) 9163 2408
info@tidewillowstudio.net.au
www.tidewillowstudio.net.au
facebook:tidewillowweddings
instagram:tidewillowweddings

Font styles to use
Serif
Sans Serif

Requirements
Nice to have
• maybe add my slogan"memories beyond eternity" if the layout looks good
Should not have
• no black color, not good idea for wedding biz card

```html
<!DOCTYPE html>
<html lang="en">
<head>
<meta charset="utf-8">
<title>Golden Hour Studio and Film – Business Card</title>
<link rel="stylesheet" href="https://fonts.googleapis.com/css2?family=Roboto:wght@400;500;700&display=swap">
<style>
  :root {
    --bg: #2e2f31;
    --gold-light: #f2c53a;
    --gold: #dca917;
    --gold-deep: #b8870c;
    --ink: #2b2114;
    --espresso: #2a1f14;
    --text-font: "Roboto", Arial, sans-serif;
  }
  * { box-sizing: border-box; margin: 0; padding: 0; }
  html, body { width: 1200px; height: 950px; overflow: hidden; }
  body {
    background: var(--bg);
    font-family: var(--text-font);
    position: relative;
  }
  .card {
    position: absolute;
    width: 620px;
    height: 354px;
    overflow: hidden;
    border-radius: 2px;
    box-shadow: 0 14px 30px rgba(0,0,0,.45);
  }

  /* Front card */
  .card--front {
    left: 110px; top: 100px;
    background: linear-gradient(135deg, var(--gold-deep) 0%, var(--gold-light) 45%, var(--gold) 70%, var(--gold-deep) 100%);
    display: flex; flex-direction: column; align-items: center; justify-content: center;
    color: var(--ink);
  }
  .brand-name {
    font-family: var(--text-font);
    font-weight: 700;
    font-size: 30px;
    line-height: 1.15;
    text-align: center;
  }
  .card--front .brand-name { color: var(--ink); max-width: 320px; }
  .social {
    margin-top: 22px;
    width: 280px;
    display: flex; align-items: center; gap: 6px;
  }
  .social__rule { flex: 1; height: 1px; background: rgba(43,33,20,.55); }
  .social__dot { width: 12px; height: 12px; border-radius: 50%; background: var(--ink); }
  .social__handle { margin-top: 8px; font-size: 14px; letter-spacing: .2px; }

  /* Back card */
  .card--back { left: 470px; top: 490px; background: var(--espresso); }
  .card--back svg.backdrop { position: absolute; inset: 0; }
  .card--back .brand-name {
    position: absolute; left: 40px; top: 124px; width: 250px;
    font-size: 28px;
    color: var(--gold-light);
  }
  .contact {
    position: absolute; right: 24px; top: 52px;
    text-align: right; color: var(--ink);
  }
  .contact__name { font-size: 16px; font-weight: 500; }
  .contact__title { font-size: 12px; margin-bottom: 12px; }
  .contact__row {
    display: flex; justify-content: flex-end; align-items: center; gap: 7px;
    font-size: 12px; line-height: 19px;
  }
  .contact__row svg { width: 12px; height: 12px; fill: var(--ink); flex: none; }
  .contact__row--plain { padding-right: 19px; }
</style>
</head>
<body>

  <section class="card card--front" aria-label="Business card front">
    <h1 class="brand-name">golden hour studio and film</h1>
    <div class="social">
      <span class="social__rule"></span>
      <span class="social__dot"></span>
      <span class="social__dot"></span>
      <span class="social__rule"></span>
    </div>
    <p class="social__handle">tidewillowweddings</p>
  </section>

  <section class="card card--back" aria-label="Business card back">
    <svg class="backdrop" viewBox="0 0 620 354" width="620" height="354" aria-hidden="true">
      <defs>
        <linearGradient id="goldSweep" x1="0" y1="0" x2="1" y2="1">
          <stop offset="0" stop-color="#b8870c"/>
          <stop offset=".45" stop-color="#f2c53a"/>
          <stop offset="1" stop-color="#c99610"/>
        </linearGradient>
      </defs>
      <path d="M620 0 L470 0 C375 8 350 150 292 238 C248 304 185 334 105 354 L620 354 Z" fill="url(#goldSweep)"/>
      <path d="M456 0 C362 10 338 148 280 234 C236 300 172 332 92 354" fill="none" stroke="#dca917" stroke-width="2"/>
    </svg>

    <h2 class="brand-name">golden hour studio and film</h2>

    <div class="contact">
      <p class="contact__name">Mara Ellison</p>
      <p class="contact__title">President</p>
      <p class="contact__row">(02) 9163 2408
        <svg viewBox="0 0 16 16"><path d="M3 1h3l1.5 4-2 1.2a8 8 0 0 0 4.3 4.3L11 8.5l4 1.5v3a2 2 0 0 1-2 2A12 12 0 0 1 1 3a2 2 0 0 1 2-2z"/></svg>
      </p>
      <p class="contact__row">(04) 3187 2259
        <svg viewBox="0 0 16 16"><path d="M4 0h8a1 1 0 0 1 1 1v14a1 1 0 0 1-1 1H4a1 1 0 0 1-1-1V1a1 1 0 0 1 1-1zm1 2v10h6V2z"/></svg>
      </p>
      <p class="contact__row">info@tidewillowstudio.net.au
        <svg viewBox="0 0 16 16"><path d="M0 3h16v10H0zm1.5 1.2L8 9l6.5-4.8V4h-13z"/></svg>
      </p>
      <p class="contact__row contact__row--plain">tidewillowstudio.net.au</p>
      <p class="contact__row">57 tarrant street, glenmore nsw 2047
        <svg viewBox="0 0 16 16"><path d="M8 0a5.5 5.5 0 0 1 5.5 5.5C13.5 10 8 16 8 16S2.5 10 2.5 5.5A5.5 5.5 0 0 1 8 0zm0 3.5a2 2 0 1 0 0 4 2 2 0 0 0 0-4z"/></svg>
      </p>
    </div>
  </section>

</body>
</html>
```